Web Design Services Create a Similar website to my Competitor

We would like a similar website designed like our main competitor with all the features there website has and more. Also we would like to accept payments through our website and to rank quickly with seo based on our home page and other page use of high traffic keywords. this is the website we would like to have ours designed similar to https://www.harbourpetalstudio.com. we will be providing the same services and more just at a different location. We would also like to know be able to easily make adjustments to the website when its time to edit it please thanks.

Basically I am looking to have have similar website built almost exactly the same but with my logo, and other personalized information to my company Rosalind Marigold Beauty Lounge. I will need to send you model images and logo design idea but the body and user interface of my competitor https://www.harbourpetalstudio.com will be exactly the same. I can be reached anytime to answer any questions you may have.
Updates

Hi Designers I would like to clarify some information Harbour Petal Studio is my Competitor we are not affiliated. I would like my website to be designed similar to hers but please do not take any content from her website to put on mine I will be providing images to be posted on my website. Also please do not use any of her videos or YouTube videos on my website to avoid any legal issues. Thanks for your understanding.

Target Market(s)

Make up Application Services For Events and Lindenbrook Summer Festival

Industry/Entity Type

Beauty and Makeup Application and services

Coding

Coded - Design and coding required

Number of Pages Required

5+ page

Font styles to use
Sans Serif

Colors
E54698
E96AAD
F1A4CE
F9D9EA
FCEFF6
A7469A
B969AE
D3A5CF
EDDBEB
F8F0F9

Requirements
Must have
• Must be similar to my competitor, need a video section, testimonial and must be easily able to navigate to information sections and book now payment notifications running on all pages so customers can easily book there spot for 2026 carnival
Nice to have
• I am looking to have a similar website to https://www.harbourpetalstudio.com created but make it as minimal and modern
Should not have
• Project can be coded if it makes it easier to create a similar look to my competitor just ask that updates can easily be made later on.

```html
<!DOCTYPE html>
<html lang="en">
<head>
<meta charset="utf-8">
<title>Rosalind Marigold Beauty Lounge</title>
<link rel="stylesheet" href="https://fonts.googleapis.com/css2?family=Oswald:wght@400;500&family=Jost:wght@400;500;600&family=Tinos:wght@700&display=swap">
<style>
:root{
  --magenta:#dd2a88;
  --pink:#e54698;
  --pink-soft:#f1a4ce;
  --pink-pale:#f9d9ea;
  --pink-mist:#fcf0f6;
  --purple:#8e2a8f;
  --purple-soft:#b969ae;
  --ink:#1d1d1f;
  --text:#333;
  --line:#e5e5e5;
  --white:#fff;
}
*{box-sizing:border-box;margin:0;padding:0}
html,body{width:1200px;height:5080px;overflow:hidden}
body{font-family:'Jost',sans-serif;color:var(--text);background:var(--white);position:relative}
.heading{font-family:'Oswald',sans-serif;font-weight:400;color:var(--ink);text-align:center}
.btn{display:inline-block;font-family:'Tinos',serif;font-weight:700;font-size:17px;color:#222;background:var(--pink-pale);border-radius:30px;padding:14px 34px;box-shadow:4px 4px 0 var(--magenta);text-decoration:none}
.rule{width:56px;height:3px;background:var(--magenta);margin:0 auto}
.photo{position:absolute}

/* header */
.site-header{position:absolute;top:0;left:0;width:1200px;height:103px;background:var(--white)}
.brand{position:absolute;left:84px;top:14px;font-weight:600;color:var(--magenta);font-size:28px;line-height:34px;width:280px}
.nav{position:absolute;left:494px;top:66px;display:flex;gap:46px;font-size:15px;color:#333}
.nav .active{color:var(--magenta);font-weight:500;border-bottom:2px solid var(--magenta);padding-bottom:4px}
.search{position:absolute;left:830px;top:13px;width:258px;height:34px;border:1px solid #999;display:flex;align-items:center;padding-left:14px;gap:12px;font-size:12px;color:#555}

/* hero */
.hero{position:absolute;top:103px;left:0;width:1200px;height:594px;background:linear-gradient(135deg,#1f6b2e 0%,#d9a21b 25%,#d23a2a 50%,#f2f2ec 62%,#c22a2a 78%,#2a6a2e 100%)}
.hero-shade{position:absolute;inset:0;background:linear-gradient(180deg,rgba(0,0,0,0) 40%,rgba(0,0,0,.45) 100%)}
.hero-copy{position:absolute;top:360px;left:0;width:1200px;text-align:center;color:var(--white)}
.hero-copy h1{font-family:'Oswald',sans-serif;font-weight:500;font-size:54px;line-height:62px}
.hero-copy p{font-size:16px;margin:10px 0 18px}
.hero-copy .btn{box-shadow:3px 3px 0 var(--magenta);padding:12px 30px}

/* events */
.events-title{position:absolute;top:734px;width:1200px;font-size:40px}
.events{position:absolute;top:813px;left:112px;display:grid;grid-template-columns:repeat(3,300px);gap:34px 38px}
.event-card{position:relative;height:312px;border-radius:18px;overflow:hidden;background:var(--purple)}
.event-card .photo{top:0;left:0;width:300px;height:250px}
.event-badge{position:absolute;right:20px;top:222px;width:42px;height:42px;border-radius:50%;background:var(--white)}
.event-info{position:absolute;left:22px;top:258px;color:var(--white)}
.event-info .date{font-size:11px}
.event-info .text{font-size:14px;font-weight:500;margin-top:6px}
.events-cta{position:absolute;top:1536px;width:1200px;text-align:center}

/* without panel */
.without{position:absolute;top:1664px;left:112px;width:976px;height:508px;background:var(--white);border-radius:40px;box-shadow:0 -4px 18px rgba(0,0,0,.08);text-align:center;padding-top:48px}
.without h2{font-size:40px;line-height:52px}
.without .rule{margin:20px auto 28px}
.without ul{list-style:none;font-size:16px;line-height:41px;color:#222}
.without li span{color:var(--magenta);margin-right:8px}
.without .nudge{color:var(--magenta);font-weight:600;font-size:18px;margin:6px 0 20px}

/* luxury */
.confetti{position:absolute;top:2235px;left:0;width:1200px;height:212px;background:linear-gradient(180deg,#fff 0%,#fdf3f7 60%,#fff 100%)}
.lux-title{position:absolute;top:2436px;width:1200px;font-size:40px;line-height:54px;color:var(--magenta)}
.lux-rule{position:absolute;top:2546px;left:572px}
.lux-copy{position:absolute;top:2586px;left:110px;width:440px;font-size:15px;line-height:25px}
.features{position:absolute;top:2722px;left:110px;display:grid;grid-template-columns:250px 200px;font-size:16px;line-height:33px;color:#222}
.features li{list-style:none;display:flex;gap:10px;align-items:flex-start}
.features li svg{margin-top:11px;flex:none}
.lux-tag{position:absolute;top:2898px;left:110px;font-family:'Oswald',sans-serif;font-weight:500;font-size:20px;color:#111}
.lux-cta{position:absolute;top:2954px;left:112px}
.lux-video{position:absolute;top:2592px;left:628px;width:500px;height:345px;background:linear-gradient(135deg,#4a7a3a 0%,#c2272d 35%,#e5b9a0 55%,#2a3a8a 75%,#c2272d 100%)}
.play{position:absolute;left:50%;top:50%;transform:translate(-50%,-50%)}

/* reviews */
.reviews{position:absolute;top:3099px;left:0;width:1200px;height:731px;background:linear-gradient(180deg,#fbe3ef 0%,#fdf2f7 60%,#fff 100%);overflow:hidden}
.reviews h2{position:absolute;top:88px;width:1200px;font-size:40px;color:var(--magenta)}
.reviews .rule{position:absolute;top:154px;left:572px}
.review-card{position:absolute;background:var(--white);border-radius:20px}
.review-card.side{top:244px;height:218px;width:300px;opacity:.45;padding:22px 20px;font-size:10px;line-height:16px;overflow:hidden}
.review-card.main{top:190px;left:207px;width:784px;height:353px;box-shadow:0 8px 0 var(--magenta),0 4px 24px rgba(0,0,0,.08);padding:30px}
.review-card .photo{left:26px;top:22px;width:296px;height:310px;border-radius:16px;background:linear-gradient(160deg,#1a8a8a 0%,#d9a521 40%,#6a3a1e 70%,#0e5e5e 100%)}
.review-body{position:absolute;left:376px;top:50px;width:380px;font-size:14px;line-height:26px;color:#222}
.review-body .quote{font-size:17px;font-weight:500;margin-bottom:12px}
.stars{color:#f2d21b;font-size:22px;letter-spacing:2px;margin:4px 0 8px}
.review-body .who{font-weight:600;font-size:15px}
.dots{position:absolute;top:616px;left:543px;display:flex;gap:10px}
.dots span{width:24px;height:5px;background:var(--pink-soft);border-radius:3px}
.dots span:first-child{width:40px;background:var(--magenta)}

/* still thinking */
.booking{position:absolute;top:3830px;left:0;width:1200px;height:647px;background:var(--magenta);text-align:center;color:var(--white)}
.booking h2{color:var(--white);font-size:40px;line-height:52px;margin-top:84px}
.booking .rule{background:var(--white);margin:18px auto 28px}
.booking p{font-size:16px;font-weight:600;line-height:31px}
.booking .btn{margin-top:28px}
.booking-video{position:absolute;top:4309px;left:112px;width:976px;height:419px;border:3px solid var(--magenta);background:linear-gradient(120deg,#4a3a2e 0%,#b47a4a 30%,#e8d8c8 50%,#8a5a3a 70%,#3a2a1e 100%)}

/* footer */
.site-footer{position:absolute;top:4777px;left:0;width:1200px;height:303px}
.footer-brand{position:absolute;left:112px;top:12px;width:300px;font-weight:600;color:var(--magenta);font-size:28px;line-height:34px}
.footer-col{position:absolute;top:14px;font-size:14px;line-height:26px;color:#333}
.footer-col h3{font-family:'Oswald',sans-serif;font-weight:500;font-size:19px;color:#111;margin-bottom:12px;line-height:26px}
.footer-col ul{list-style:none}
.email-field{width:228px;border-bottom:1px solid #999;font-size:11px;color:#666;padding:4px 0 6px;margin:8px 0 30px}
.copyright{position:absolute;top:262px;left:112px;width:976px;border-top:1px solid var(--line);padding-top:14px;text-align:center;font-size:14px;color:#222}
</style>
</head>
<body>

<header class="site-header">
  <div class="brand">Rosalind Marigold<br>Beauty Lounge</div>
  <nav class="nav">
    <span class="active">Home</span><span>Glam Anywhere</span><span>Glam Store</span><span>Blog</span><span>Reviews</span><span>More ⌄</span>
  </nav>
  <div class="search">
    <svg width="12" height="12" viewBox="0 0 12 12"><circle cx="5" cy="5" r="3.8" fill="none" stroke="#222" stroke-width="1.6"/><line x1="8" y1="8" x2="11" y2="11" stroke="#222" stroke-width="1.6"/></svg>
    Search..............
  </div>
</header>

<section class="hero" role="img" aria-label="Two festival dancers in feathered headdresses and jewelled costumes among tropical leaves">
  <div class="hero-shade"></div>
  <div class="hero-copy">
    <h1>Get Carnival-Ready with Rosalind Marigold<br>Beauty Lounge</h1>
    <p>Our All-In-One Carnival Beauty Concierge, Because You Deserve a Stress-Free Start to the Road.</p>
    <span class="btn">Book Now</span>
  </div>
</section>

<h2 class="heading events-title">Carnival Festival</h2>
<div class="events">
  <article class="event-card"><div class="photo" role="img" aria-label="Dancer in blue and gold festival costume" style="background:linear-gradient(150deg,#1b2a8a,#c9a227 50%,#6a2a8a)"></div><span class="event-badge"></span><div class="event-info"><div class="date">18 October 2024</div><div class="text">Lorem ipsum dolor sit amet,</div></div></article>
  <article class="event-card"><div class="photo" role="img" aria-label="Smiling festival-goer in red feathered headdress" style="background:linear-gradient(150deg,#e0452a,#a8201e 50%,#e6862a)"></div><span class="event-badge"></span><div class="event-info"><div class="date">22 May 2025</div><div class="text">Lorem ipsum dolor sit amet,</div></div></article>
  <article class="event-card"><div class="photo" role="img" aria-label="Dancer in red and white costume amid confetti" style="background:linear-gradient(150deg,#2a1a1a,#b8242a 50%,#e8dada)"></div><span class="event-badge"></span><div class="event-info"><div class="date">18 June 2025</div><div class="text">Lorem ipsum dolor sit amet,</div></div></article>
  <article class="event-card"><div class="photo" role="img" aria-label="Laughing dancer in golden feathered costume" style="background:linear-gradient(150deg,#6a4a1a,#e0a83a 50%,#3a2a1a)"></div><span class="event-badge"></span><div class="event-info"><div class="date">10 October 2024</div><div class="text">Lorem ipsum dolor sit amet,</div></div></article>
  <article class="event-card"><div class="photo" role="img" aria-label="Dancer in multicolour headdress at night parade" style="background:linear-gradient(150deg,#c8502a,#e8c04a 45%,#4a2a4a)"></div><span class="event-badge"></span><div class="event-info"><div class="date">08 April 2025</div><div class="text">Lorem ipsum dolor sit amet,</div></div></article>
  <article class="event-card"><div class="photo" role="img" aria-label="Festival dancer in gold costume with warm lights" style="background:linear-gradient(150deg,#8a5a1a,#d8a03a 50%,#2a1a10)"></div><span class="event-badge"></span><div class="event-info"><div class="date">24 July 2025</div><div class="text">Lorem ipsum dolor sit amet,</div></div></article>
</div>
<div class="events-cta"><span class="btn">Choose Your Destination</span></div>

<section class="without">
  <h2 class="heading">Without Rosalind Marigold Hub, your Carnival<br>morning might look like this:</h2>
  <div class="rule"></div>
  <ul>
    <li><span>✖</span>4am makeup appointment across town</li>
    <li><span>✖</span>Rushing to a hairstylist who's running late</li>
    <li><span>✖</span>Trying to lace up a frontline costume alone</li>
    <li><span>✖</span>Now you're sweating out your beat before you hit the road</li>
  </ul>
  <p class="nudge">Don't do this to yourself ➔</p>
  <span class="btn">See Packages</span>
</section>

<div class="confetti" role="img" aria-label="Scattered colourful confetti"></div>
<h2 class="heading lux-title">With Rosalind Marigold Hub, It's a luxury prep lounge,<br>not a panic room</h2>
<div class="rule lux-rule"></div>
<p class="lux-copy">Marigold Hub is your go-to destination for luxurious Carnival makeup, hair and photos founded by pro-MUA Tessa Rowland since 2017. Our services are designed to make you feel like the Queen you are with everything under one roof:</p>
<ul class="features">
  <li><svg width="12" height="10" viewBox="0 0 12 10"><path d="M1 5l3.5 3.5L11 1" fill="none" stroke="#dd2a88" stroke-width="2.4"/></svg>Pro Makeup</li>
  <li><svg width="12" height="10" viewBox="0 0 12 10"><path d="M1 5l3.5 3.5L11 1" fill="none" stroke="#dd2a88" stroke-width="2.4"/></svg>Photoshoot Reels</li>
  <li><svg width="12" height="10" viewBox="0 0 12 10"><path d="M1 5l3.5 3.5L11 1" fill="none" stroke="#dd2a88" stroke-width="2.4"/></svg>Shuttle Seamstress.</li>
  <li><svg width="12" height="10" viewBox="0 0 12 10"><path d="M1 5l3.5 3.5L11 1" fill="none" stroke="#dd2a88" stroke-width="2.4"/></svg>Dressing Assistants</li>
  <li><svg width="12" height="10" viewBox="0 0 12 10"><path d="M1 5l3.5 3.5L11 1" fill="none" stroke="#dd2a88" stroke-width="2.4"/></svg>Refreshments</li>
  <li><svg width="12" height="10" viewBox="0 0 12 10"><path d="M1 5l3.5 3.5L11 1" fill="none" stroke="#dd2a88" stroke-width="2.4"/></svg>Coffee &amp; Tea</li>
  <li><svg width="12" height="10" viewBox="0 0 12 10"><path d="M1 5l3.5 3.5L11 1" fill="none" stroke="#dd2a88" stroke-width="2.4"/></svg>Carnival Hair Dressing<br>Rooms</li>
  <li><svg width="12" height="10" viewBox="0 0 12 10"><path d="M1 5l3.5 3.5L11 1" fill="none" stroke="#dd2a88" stroke-width="2.4"/></svg>Bag Check</li>
</ul>
<p class="lux-tag">Comprehensive Carnival Prep—Tailored Just for You.</p>
<div class="lux-cta"><span class="btn">Yes, I Need This</span></div>
<div class="lux-video" role="img" aria-label="Video preview of a group of dancers in feathered festival costumes">
  <svg class="play" width="72" height="72" viewBox="0 0 72 72"><circle cx="36" cy="36" r="36" fill="#dd2a88"/><path d="M29 23l22 13-22 13z" fill="#fff"/></svg>
</div>

<section class="reviews">
  <h2 class="heading">Real Stories from Our Rosalind Marigold Fam</h2>
  <div class="rule"></div>
  <div class="review-card side" style="left:-120px">"Absolutely flawless!"<br>"Rosalind and her team made me feel like a Carnival queen! My makeup stayed perfect all day—even in the heat. I got so many compliments. Can't wait to book again for 2026!"<br><span style="color:#f2d21b">★★★★★</span><br>IMANI L., LINDENBROOK</div>
  <div class="review-card side" style="left:980px">"Absolutely flawless!"<br>"Rosalind and her team made me feel like a Carnival queen! My makeup stayed perfect all day—even in the heat. I got so many compliments. Can't wait to book again for 2026!"<br><span style="color:#f2d21b">★★★★★</span><br>IMANI L., LINDENBROOK</div>
  <div class="review-card main">
    <div class="photo" role="img" aria-label="Portrait of a woman in a jewelled gold and teal festival headdress"></div>
    <div class="review-body">
      <p class="quote">"Absolutely flawless!"</p>
      <p>"Rosalind and her team made me feel like a Carnival queen! My makeup stayed perfect all day—even in the heat. I got so many compliments. Can't wait to book again for 2026!" "The vibes, the professionalism, the results—everything was top-tier. Booking was easy, and the payment confirmation came instantly. 10/10!"</p>
      <div class="stars">★★★★★</div>
      <p class="who">IMANI L., LINDENBROOK</p>
    </div>
  </div>
  <div class="dots"><span></span><span></span><span></span></div>
</section>

<section class="booking">
  <h2 class="heading">Still thinking? The girls who booked already know - the road<br>hits different when Rosalind Marigold Hub's<br>behind the scenes.</h2>
  <div class="rule"></div>
  <p>Early times gone. Your costume strings make<br>no sense. And the MUA you wanted? Already fully booked. Don't play yourself.</p>
  <span class="btn">See Availability Now</span>
</section>
<div class="booking-video" role="img" aria-label="Video preview of a dancer in a beaded festival costume">
  <svg class="play" width="72" height="72" viewBox="0 0 72 72"><circle cx="36" cy="36" r="36" fill="#dd2a88"/><path d="M29 23l22 13-22 13z" fill="#fff"/></svg>
</div>

<footer class="site-footer">
  <div class="footer-brand">Rosalind Marigold<br>Beauty Lounge</div>
  <div class="footer-col" style="left:478px">
    <h3>Quick Links</h3>
    <ul><li>Home</li><li>Glam Anywhere</li><li>Glam Store</li><li>Blog</li><li>Reviews</li><li>Contact Us</li></ul>
  </div>
  <div class="footer-col" style="left:636px;width:210px">
    <h3>Contact Us</h3>
    <p>Location: Rosalind Marigold Beauty Lounge, Us</p>
    <p>Mail Us: info@rmbeauty.com</p>
    <p>Phone: +1 555 214 0387</p>
  </div>
  <div class="footer-col" style="left:860px;width:230px">
    <h3>Subscribe to get exclusive updates</h3>
    <div class="email-field">Email</div>
    <span class="btn" style="font-size:15px;padding:10px 22px">Join our Mailing List</span>
  </div>
  <div class="copyright">Copyrights@2025.Rosalind Marigold Beauty Lounge.All Rights Reserved</div>
</footer>

</body>
</html>
```